Super elegant, crisp & clean Business card design required

We recently upgraded our branding - which is on our website - talvendoraphoto.com

I would like a simple, yet elegant, clean business card design please.

The font of my logo is Cinzel - and because of the natural colour - it's best to have this on a black background.

I would like to have the back of the business card - with simply my logo.

PLEASE DO NOT SUBMIT A COMPLICATED / UNCLEAN DESIGN

Industry/Entity Type

Business

Contact Information for Business Card

Talven Doroshko Photography

Font styles to use
Other font styles liked:
• Cinzel

Requirements
Must have
• A backpage with nothing but my logo
• Simple design - stands out
Should not have
• Colour that dont align with my logo
• Over complicated '/ non symmetrical design

```html
<!DOCTYPE html>
<html lang="en">
<head>
<meta charset="UTF-8">
<title>Talven Doroshko Photography – Business Card</title>
<link rel="stylesheet" href="https://fonts.googleapis.com/css2?family=Cinzel:wght@400&family=Open+Sans:wght@400;600&display=swap">
<style>
  :root {
    --backdrop: #2b2521;
    --card: #151515;
    --gold: #8c7656;
    --gold-line: #7a6749;
    --ink-light: #f2f2f2;
    --card-w: 540px;
    --card-h: 309px;
  }
  * { box-sizing: border-box; margin: 0; padding: 0; }
  html, body {
    width: 1200px;
    height: 844px;
    overflow: hidden;
    background: var(--backdrop);
  }
  .stage {
    position: relative;
    width: 1200px;
    height: 844px;
    display: flex;
    align-items: center;
    justify-content: center;
    gap: 40px;
  }
  .card {
    position: relative;
    width: var(--card-w);
    height: var(--card-h);
    background: var(--card);
    box-shadow: 0 10px 30px rgba(0,0,0,0.45);
  }
  .wordmark {
    font-family: "Cinzel", serif;
    font-weight: 400;
    color: var(--gold);
    text-align: center;
    line-height: 1.15;
  }
  .wordmark .name-line { display: block; }
  .wordmark .sub-line { display: block; letter-spacing: 0.55em; }

  /* front */
  .card-front .wordmark {
    position: absolute;
    top: 40px;
    left: 130px;
    right: 20px;
    font-size: 22px;
  }
  .card-front .wordmark .sub-line { font-size: 22px; letter-spacing: 0.5em; margin-top: -2px; }
  .card-front .divider {
    position: absolute;
    top: 122px;
    left: 0;
    right: 0;
    height: 1px;
    background: var(--gold-line);
  }
  .holder {
    position: absolute;
    top: 150px;
    left: 30px;
    font-family: "Open Sans", sans-serif;
  }
  .holder-name {
    color: var(--gold);
    font-weight: 600;
    font-size: 17px;
    line-height: 1.2;
  }
  .holder-role {
    color: var(--ink-light);
    font-size: 13px;
    line-height: 1.3;
  }
  .holder-rule {
    position: absolute;
    top: 198px;
    left: 0;
    width: 230px;
    height: 1px;
    background: var(--gold-line);
  }
  .contact-list {
    position: absolute;
    top: 210px;
    left: 30px;
    list-style: none;
    font-family: "Open Sans", sans-serif;
    font-size: 14px;
    line-height: 21px;
    color: var(--ink-light);
  }

  /* back */
  .card-back {
    display: flex;
    flex-direction: column;
    align-items: center;
    justify-content: center;
  }
  .card-back .wordmark { font-size: 26px; }
  .card-back .wordmark .sub-line { font-size: 26px; letter-spacing: 0.5em; }
</style>
</head>
<body>
  <main class="stage">
    <section class="card card-front" aria-label="Business card front">
      <div class="wordmark">
        <span class="name-line">Talven Doroshko</span>
        <span class="sub-line">Photography</span>
      </div>
      <div class="divider"></div>
      <div class="holder">
        <p class="holder-name">Elias Marlowe</p>
        <p class="holder-role">Managing Director</p>
      </div>
      <div class="holder-rule"></div>
      <ul class="contact-list">
        <li>(021)-384-5170 &nbsp;|&nbsp; 482-613-2095</li>
        <li>info@talvendoraphoto.com</li>
        <li>www.talvendoraphoto.com</li>
        <li>48 Harbour Lane, Studio Quarter, 560214</li>
      </ul>
    </section>

    <section class="card card-back" aria-label="Business card back">
      <div class="wordmark">
        <span class="name-line">Talven Doroshko</span>
        <span class="sub-line">Photography</span>
      </div>
    </section>
  </main>
</body>
</html>
```